Website Design for a different kind of Business Consulting organisation needed!

We need a website design that reflects who we are, the simplicity of our consulting business and with a focus on our priority - to help our clients deliver, or execute - the "e" in Vantor-i.

Our key high level requirements are:
1) Simple and intuitive look and feel
2) Integration with all key social media platforms, twitter, facebook, linkedin, tumblr.

10 pages, tops.
- Main page - Welcome
- About Us/ Who are Vantor-i?
- 5 services pages - Project Management, Business Process Management, Change Management, Business Analysis and Finance Systems
- Contact Us

Something like:
http://www.lumvexhold.example/

Vantor-i is a registered trademark and all Logos and other branded material are attached for reference.

So, what’s our gig: A few snippets from previous work...

We are a different kind of business consulting group. We partner with our clients to help them deliver change. We don't just provide them with the theory. We also provide them with the leadership and capability to execute the change.

We aren’t a one stop shop, and we don’t offer cookie cutter solutions. We’re a boutique consulting firm covering Project Management, Business Process Management, Change Management and Business Analytics.

Vantor-i is a professional services organisation that partners with their clients to lead the execution of strategic process and system improvement initiatives. Vantor-i combines hands on delivery with coaching in best practice methodologies and approaches to build their clients capabilities to ensure their ongoing success in project implementations.

UPDATES:

Thanks to everyone who has submitted designs so far. The standard of designs coming through is quite high, with lots of professional designs that nail the design brief. Eliminating them is proving to be quite challenging.

A few updates to the job brief:
- Please make sure the design fits on one page. We would like all of our information to be on the first page that people see without them having to scroll down
- Please ensure you include the FIVE services we offer in the design
- Please use corporate images/istock photos in your designs which are relevant to our business
- Please add a section for a live twitter feed from our twitter account and a link to google+
- Please add a section for news/updates

Also, if you are able to build a site once a design is selected, please let us know.

Thanks,

Maribel.

Target Market(s)

Our target customers are large enterprises in Australia that are growing rapidly and have recently (last 24 months) undertaken or are currently undergoing software implementations and business process improvement programs. These businesses have a turnover of $100m or above and are working hard to differentiate themselves from their competitors but are not seeing the return on investment promised by software vendors and process improvement initiatives.

Industry/Entity Type

Leadership

Requirements
Must have
• Collaboration / Training / Workshop / Consulting images all of a professional nature.
Simple, non-cluttered look with plenty of white space.

```html
<!DOCTYPE html>
<html lang="en">
<head>
<meta charset="utf-8">
<title>Vantor-i — Business Consulting</title>
<link rel="stylesheet" href="https://fonts.googleapis.com/css2?family=Roboto+Condensed:wght@300;400&family=Arimo:ital,wght@0,400;1,400&display=swap">
<style>
:root{
  --blue-deep:#003a8c;
  --blue:#0a4ea8;
  --blue-mid:#0e5cb8;
  --blue-bright:#1070c8;
  --blue-link:#1a8fd8;
  --ink:#222;
  --body:#6a6a6a;
  --grey-panel:#e8e8e8;
  --grey-footer:#ececec;
  --grey-line:#d8d8d8;
  --white:#fff;
}
*{margin:0;padding:0;box-sizing:border-box}
a{text-decoration:none}
html,body{width:1200px;height:1154px;overflow:hidden;background:var(--white)}
body{position:relative;font-family:"Arimo",Arial,sans-serif;color:var(--body)}
.top-rule{position:absolute;left:0;top:0;width:1200px;height:6px;background:var(--blue-deep)}
.brand{position:absolute;left:200px;top:24px;display:flex;align-items:flex-end;gap:6px}
.brand-name{font-family:"Roboto Condensed",sans-serif;font-weight:400;font-size:46px;line-height:46px;color:var(--blue)}
.brand-tag{font-family:"Arimo",Arial,sans-serif;font-size:8px;color:var(--blue);margin-bottom:4px}
.header-band{position:absolute;left:0;top:0}
.main-nav{position:absolute;top:0;left:641px;height:91px;display:flex}
.main-nav a{display:flex;align-items:center;justify-content:center;height:91px;font-family:"Roboto Condensed",sans-serif;font-weight:300;font-size:15px;color:var(--white)}
.nav-home{width:73px}
.nav-about{width:81px;background:var(--blue-mid)}
.nav-services{width:108px;background:#0a66c0}
.nav-contact{width:97px;background:var(--blue-bright)}
.hero{position:absolute;left:200px;top:91px;width:800px;height:325px}
.hero-photo{position:absolute;inset:0;background:linear-gradient(90deg,#c9ccd2 0%,#e6e9ee 45%,#f2f3f5 100%)}
.hero-copy{position:absolute;left:577px;top:199px;color:var(--white);font-family:"Roboto Condensed",sans-serif;font-weight:300;white-space:nowrap}
.hero-copy h1{font-weight:300;font-size:24px;line-height:28px}
.hero-copy p{font-size:14px;line-height:18px;margin-top:2px}
.hero-more{position:absolute;right:32px;top:259px;color:var(--white);font-family:"Roboto Condensed",sans-serif;font-size:12px}
.hero-dots{position:absolute;left:370px;top:291px;display:flex;gap:4px}
.hero-dots span{width:12px;height:12px;border-radius:50%;background:var(--white)}
.hero-dots span.on{background:var(--blue)}
.feature{position:absolute;top:433px;width:256px;height:170px}
.feature-photo{position:absolute;inset:0;background:linear-gradient(180deg,#d6d9de,#aeb4bc)}
.feature-bar{position:absolute;left:0;bottom:0;width:256px;height:32px;background:rgba(10,78,168,.92);display:flex;align-items:center}
.feature-bar span{flex:1;padding-left:11px;font-family:"Roboto Condensed",sans-serif;font-weight:300;font-size:20px;color:var(--white);white-space:nowrap}
.feature-bar svg{width:32px;height:32px;background:var(--blue-bright)}
.welcome{position:absolute;left:201px;top:660px;width:515px}
.welcome h2{font-family:"Roboto Condensed",sans-serif;font-weight:300;font-size:27px;color:var(--blue);line-height:32px}
.welcome p{font-size:11px;line-height:17px;margin-top:13px;white-space:nowrap}
.welcome p+p{margin-top:16px}
.divider{position:absolute;left:736px;top:656px;width:1px;height:260px;background:var(--grey-line)}
.tweets{position:absolute;left:779px;top:658px;width:221px;height:254px;background:var(--grey-panel);padding:16px 6px 0 15px}
.tweets h3{font-family:"Arimo",Arial,sans-serif;font-weight:400;font-size:14px;line-height:16px;color:var(--ink)}
.tweet{position:relative;padding-left:24px;margin-top:6px;font-size:10px;line-height:14px;color:#555;white-space:nowrap}
.tweet+.tweet{margin-top:13px}
.tweet::before{content:"";position:absolute;left:2px;top:1px;width:14px;height:14px;border-radius:50%;background:#333}
.tweet.live::before{background:var(--blue-link)}
.tweet a{color:var(--blue-link);display:block}
.tweet em{color:#333;display:block}
.footer{position:absolute;left:0;top:968px;width:1200px;height:186px;background:var(--grey-footer)}
.footer-brand{position:absolute;left:200px;top:45px;display:flex;align-items:flex-end;gap:4px}
.footer-brand .brand-name{font-size:30px;line-height:30px;color:#6d6d6d}
.footer-brand .brand-tag{font-size:6px;color:#6d6d6d;margin-bottom:2px}
.social{position:absolute;left:200px;top:98px;display:flex;gap:6px}
.social span{width:27px;height:27px;border-radius:50%;background:#a9a9a9}
.social span.first{background:#6cc3ef}
.footer-col{position:absolute;top:41px;list-style:none;font-size:10px;line-height:21px;color:#555}
</style>
</head>
<body>
<div class="top-rule"></div>

<svg class="header-band" width="1200" height="416" viewBox="0 0 1200 416" aria-hidden="true">
  <polygon points="600,6 1000,6 1000,91 641,91" fill="var(--blue-deep)"/>
</svg>

<a class="brand" href="#"><span class="brand-name">Vantor-i</span><span class="brand-tag">Pty Ltd</span></a>

<nav class="main-nav">
  <a class="nav-home" href="#">Home</a>
  <a class="nav-about" href="#">About Us</a>
  <a class="nav-services" href="#">Our Services</a>
  <a class="nav-contact" href="#">Contact Us</a>
</nav>

<section class="hero">
  <div class="hero-photo" role="img" aria-label="Photo of a smiling businessman in front of colleagues working at a laptop"></div>
  <svg style="position:absolute;inset:0" width="800" height="325" viewBox="0 0 800 325" aria-hidden="true">
    <polygon points="441,0 800,0 800,325 590,325" fill="var(--blue)" opacity=".95"/>
    <polygon points="520,0 725,0 530,240" fill="var(--blue-bright)" opacity=".35"/>
    <polygon points="441,0 520,0 590,325 560,325" fill="#2e78cf" opacity=".4"/>
  </svg>
  <div class="hero-copy">
    <h1>Lorem ipsum dolor sit</h1>
    <p>Consectetur adipiscing elit.</p>
  </div>
  <a class="hero-more" href="#">Read more &#8250;</a>
  <div class="hero-dots"><span class="on"></span><span></span><span></span><span></span></div>
</section>

<a class="feature" style="left:200px" href="#">
  <div class="feature-photo" role="img" aria-label="Photo of a senior executive with his team"></div>
  <div class="feature-bar"><span>Lorem ipsum dolor sit</span><svg viewBox="0 0 32 32" aria-hidden="true"><path d="M13 10l6 6-6 6" fill="none" stroke="#fff" stroke-width="2"/></svg></div>
</a>
<a class="feature" style="left:472px" href="#">
  <div class="feature-photo" role="img" aria-label="Photo of colleagues in discussion in a bright office"></div>
  <div class="feature-bar"><span>Lorem ipsum dolor sit</span><svg viewBox="0 0 32 32" aria-hidden="true"><path d="M13 10l6 6-6 6" fill="none" stroke="#fff" stroke-width="2"/></svg></div>
</a>
<a class="feature" style="left:744px" href="#">
  <div class="feature-photo" role="img" aria-label="Photo of a customer support team wearing headsets"></div>
  <div class="feature-bar"><span>Lorem ipsum dolor sit</span><svg viewBox="0 0 32 32" aria-hidden="true"><path d="M13 10l6 6-6 6" fill="none" stroke="#fff" stroke-width="2"/></svg></div>
</a>

<section class="welcome">
  <h2>Welcome to Vantor-i</h2>
  <p>Lorem ipsum dolor sit amet, consectetur adipiscing elit. Nulla lobortis consequat mauris, eget eleifend nunc<br>viverra viverra. Ut ac risus odio. Aliquam pretium purus sed nulla feugiat blandit. Cras vel libero ut lacus<br>eleifend tempor. Phasellus eleifend, magna non tincidunt accumsan, justo arcu cursus ipsum,</p>
  <p>non porttitor sapien quam vel magna. Maecenas elit nisl, molestie nec dapibus nec, aliquet a erat. Donec<br>scelerisque lacus a libero suscipit auctor volutpat enim euismod. Mauris porta,</p>
  <p>Lacus ut ullamcorper sodales, mauris tortor feugiat purus, nec aliquam neque purus ac metus. Nunc eleifend<br>leo quis nisl hendrerit ultrices. Suspendisse quis feugiat elit. Fusce vitae dolor ac est tincidunt feugiat. Pha-<br>sellus volutpat dui in sapien malesuada tempus placerat justo ultricies. Duis mollis ornare risus, ut consect-<br>etur mi tincidunt sit amet. Maecenas quis nibh ac orci tempus scelerisque ac et massa.</p>
</section>

<div class="divider"></div>

<aside class="tweets">
  <h3>Latest Tweets</h3>
  <div class="tweet">Lorem ipsum dolor sit amet, consectetu<br>adipiscing elit, sed diam nonummy nibh<a href="#">http://vantor-i.example/</a><em>24 minutes ago</em></div>
  <div class="tweet">Lorem ipsum dolor sit amet, consectetu<br>adipiscing elit, sed diam nonummy nibh<a href="#">http://vantor-i.example/</a><em>28 minutes ago</em></div>
  <div class="tweet live">Lorem ipsum dolor sit amet, consecte<br>adipiscing elit, sed diam nonummy<a href="#">http://vantor-i.example/</a><em>29 minutes ago</em></div>
</aside>

<footer class="footer">
  <div class="footer-brand"><span class="brand-name">Vantor-i</span><span class="brand-tag">Pty Ltd</span></div>
  <div class="social" aria-label="Social media links"><span class="first"></span><span></span><span></span><span></span></div>
  <ul class="footer-col" style="left:387px"><li>Home</li><li>About Us</li><li>Our Services</li><li>Contact Us</li></ul>
  <ul class="footer-col" style="left:499px"><li>Lorem ipsum</li><li>Dolor sit</li><li>Amet, consectetur</li><li>Adipiscing</li><li>Elit. Nulla</li></ul>
  <ul class="footer-col" style="left:635px"><li>lobortis consequat</li><li>Mauris, eget</li><li>Eleifend nunc</li><li>Viverra viverra</li></ul>
  <ul class="footer-col" style="left:779px"><li>Lorem ipsum</li><li>Dolor sit</li><li>Amet, consectetur</li><li>Adipiscing</li><li>Elit. Nulla</li></ul>
  <ul class="footer-col" style="left:907px"><li>lobortis consequat</li><li>Mauris, eget</li><li>Eleifend nunc</li><li>Viverra viverra</li></ul>
</footer>
</body>
</html>
```